Renny Oskow - Free Personalised Health Consultation - "One size does not fit all"

This flyer will be left on tables/seats at speaking events and seminars and used to attain leads.

Top half will have "SMS me for a FREE Personalised Health Consultation" and my picture (see www.rennyoskow-demo.com and pick most engaging photo) and underneath my contact details. It must have lines with "Notes:" halfway down so people can take notes at the seminar and lines on the back with my contact details again and "Notes: with lines.

I am having a business card also being designed by Artvane for same and would like the flyer and business card to carry a similar feel/look for consistency.

Below is the brief for the business card being designed:
Business Card for www.rennyoskow-demo.com site. It is a trust site and I use it for 1:1 relatable connections. It is the one I use for building intimate 1:1 trust building and Exec Coaching Services and programs for high wealth individuals and corporates. I also have a commercial programmatic site of my personal health products and services and programs for main stream one to many. www.steadyforwardliving-demo.com that can also provoke thought for the www.rennyoskow-demo.com business card. (mind you will get a separate business card for that site, but want to provide context). It has a logo which you may want to draw from in designing the rennyoskow business card which is personal and is about building my brand. There is also a rennyoskow personal PX page and rennyoskow business PX page. I am a Certified Talent Compass 3.1 Coach with Norvik and you can get a corporate brief of me on there to give you more context https://www.norvikcoachhub-demo.com/coach/en-us/directory?search=renny

Target Market(s)

Exec, IT, Health conscious. Corporates wanting to run Health and Wellness programs. Those wanting to go from good to great. Millennials to Middleaged.

Industry/Entity Type

Health And Wellness

Font styles to use
Sans Serif
Other font styles liked:
• Arial and Calibri ok too

Colors

Designer to choose colors to be used in the design.

Requirements
Must have
• Picture of me - use best from www.rennyoskow-demo.com or can send one you choose.
• Contact details like my buisness card being designed by you guys in separate project.
• Name: Renny Oskow
• email: renny@rennyoskow-demo.,com
• Phone: Australia +61 400 000 137 Singapore: +65 9000 2468
Nice to have
• Open to ideas

```html
<!DOCTYPE html>
<html lang="en">
<head>
<meta charset="utf-8">
<title>Renny Oskow – Health Goal Chat Card</title>
<link rel="stylesheet" href="https://fonts.googleapis.com/css2?family=Oswald:wght@600&family=Montserrat:wght@300;500&family=Arimo&family=Nothing+You+Could+Do&display=swap">
<style>
  :root {
    --page: #e9e7e4;
    --card: #ffffff;
    --ink-dark: #262626;
    --ink-light: #ffffff;
    --rule: #9a9a9a;
    --photo-light: #d9d9d9;
    --photo-mid: #a8a8a8;
    --photo-dark: #5c5c5c;
  }
  * { margin: 0; padding: 0; box-sizing: border-box; }
  html, body { width: 1200px; height: 903px; overflow: hidden; }
  body { background: var(--page); position: relative; }

  .card {
    position: absolute;
    left: 331px;
    width: 538px;
    height: 314px;
    background: var(--card);
    overflow: hidden;
    box-shadow: 0 2px 6px rgba(0,0,0,0.18);
  }
  .card--front { top: 122px; }
  .card--back { top: 467px; }

  .hero-photo {
    position: absolute;
    left: 0; top: 0;
    width: 538px; height: 272px;
    background: linear-gradient(100deg, var(--photo-light) 0%, var(--photo-mid) 45%, var(--photo-dark) 65%, var(--photo-light) 100%);
  }
  .shapes { position: absolute; left: 0; top: 0; width: 538px; height: 314px; }

  .signature {
    position: absolute;
    left: 62px; top: 42px;
    font-family: "Nothing You Could Do", cursive;
    font-size: 21px;
    color: var(--ink-light);
    white-space: nowrap;
  }
  .headline {
    position: absolute;
    left: 31px; top: 86px;
    font-family: "Oswald", sans-serif;
    font-weight: 600;
    font-size: 24px;
    line-height: 1;
    letter-spacing: 0.2px;
    color: var(--ink-light);
    transform: scaleY(1.08);
    transform-origin: left top;
  }
  .email-line {
    position: absolute;
    left: 31px; top: 118px;
    font-family: "Montserrat", sans-serif;
    font-weight: 300;
    font-size: 18px;
    color: var(--ink-light);
    white-space: nowrap;
  }
  .offer {
    position: absolute;
    left: 31px; top: 156px;
    width: 240px;
    font-family: "Montserrat", sans-serif;
    font-weight: 500;
    font-size: 15px;
    line-height: 20px;
    color: var(--ink-light);
  }

  .footer-band { position: absolute; left: 0; top: 270px; width: 538px; height: 44px; }
  .pillars {
    position: absolute;
    left: 20px; top: 0;
    line-height: 44px;
    font-family: "Arimo", sans-serif;
    font-size: 13.5px;
    color: var(--ink-light);
    white-space: nowrap;
  }
  .website {
    position: absolute;
    left: 342px; top: 0;
    line-height: 40px;
    font-family: "Arimo", sans-serif;
    font-size: 14.5px;
    color: var(--ink-dark);
    white-space: nowrap;
  }

  .notes-title {
    position: absolute;
    left: 18px; top: 20px;
    font-family: "Montserrat", sans-serif;
    font-weight: 500;
    font-size: 15px;
    letter-spacing: 0.5px;
    color: var(--ink-dark);
  }
  .note-line {
    position: absolute;
    left: 18px;
    width: 500px;
    border-top: 1px dotted var(--rule);
  }
</style>
</head>
<body>

<section class="card card--front">
  <div class="hero-photo" role="img" aria-label="Black and white photo of Renny Oskow in a dark suit leaning on a bicycle beside a white bench on a shopfront walkway"></div>
  <svg class="shapes" viewBox="0 0 538 314" aria-hidden="true">
    <polygon points="0,20 257,20 305,126 257,251 0,251" fill="var(--ink-dark)"/>
    <polygon points="0,270 538,270 538,314 0,314" fill="var(--ink-dark)"/>
    <polygon points="339,275 538,275 538,314 326,314" fill="var(--card)"/>
  </svg>
  <div class="signature">Renny Oskow</div>
  <div class="headline">EMAIL ME AT CONNECT</div>
  <div class="email-line">@rennyoskow-demo.com</div>
  <p class="offer">to connect for a no charge Personalised health goal chat</p>
  <div class="footer-band">
    <span class="pillars">Health &gt; Performance &gt; Longevity &gt; Wellbeing</span>
    <span class="website">www.rennyoskow-demo.com</span>
  </div>
</section>

<section class="card card--back">
  <svg class="shapes" viewBox="0 0 538 314" aria-hidden="true">
    <polygon points="0,270 538,270 538,314 0,314" fill="var(--ink-dark)"/>
    <polygon points="339,275 538,275 538,314 326,314" fill="var(--card)"/>
  </svg>
  <h2 class="notes-title">NOTES</h2>
  <div class="note-line" style="top:59px"></div>
  <div class="note-line" style="top:97px"></div>
  <div class="note-line" style="top:134px"></div>
  <div class="note-line" style="top:172px"></div>
  <div class="note-line" style="top:210px"></div>
  <div class="note-line" style="top:246px"></div>
  <div class="footer-band">
    <span class="pillars">Health &gt; Performance &gt; Longevity &gt; Wellbeing</span>
    <span class="website">www.rennyoskow-demo.com</span>
  </div>
</section>

</body>
</html>
```